Corvane Lending Partners. Professional and Established Company

A full service finance company specializing in obtaining capital for small business. Business Lending advisor, helping small business owners access the capital they need to launch, grow, or sustain their business. Many of our programs offer flexible guidelines to overcome common obstacles such as credit score, credit history, and time in business, financials, and industry type. Our streamlined funding process makes getting a business loan, business line of credit, stated income commercial real estate loan, a smooth and stress free experience.SOME OF THE MOST COMMON NEEDS FOR BUSINESS CAPITAL:• Working Capital• Debt Consolidations (loans, merchant cash advances, etc.)• Payroll• Operating Expenses• Inventory• Equipment Financing• Commercial Real Estate (Purchase, Fix & Flip, Rehab, Renovations)• Business Acquisitions• Business ExpansionWe like the websites:www.quillmorecf.com they are in the same industry and provide the same servicesWe are wanting to be able to update when we do press releases and such using Word Press. Our look should be very professional and we will be adding Our Team Professional Bios and Headshots.

Industry/Entity Type

Finance

Number of Pages Required

5+ page

Font styles to use
Serif
Sans Serif

Requirements
Must have
• We want to copy quillmorecf.com
• We need:
• Home Page
• About Us
• Loan Programs
• Loan Criteria
• News
• Apply Now
• Contact
Nice to have
• See quillmorecf.com
Should not have
• Need professional design. Nothing bright or abstract

```html
<!DOCTYPE html>
<html lang="en">
<head>
<meta charset="utf-8">
<title>Corvane Lending Partners</title>
<link href="https://fonts.googleapis.com/css2?family=Poppins:wght@300;400;500;600&family=Cormorant+Garamond:wght@500;600&display=swap" rel="stylesheet">
<style>
:root{
  --blue:#2a6fb6;
  --blue-dark:#1f5c9a;
  --ink:#333a44;
  --muted:#7b828b;
  --grey-bg:#f1f1f1;
  --field:#ececec;
  --footer:#1c1c1c;
  --white:#ffffff;
}
*{margin:0;padding:0;box-sizing:border-box}
html,body{width:1200px;height:3922px;overflow:hidden}
body{font-family:'Poppins',sans-serif;color:var(--ink);background:var(--white);position:relative}
a{color:inherit;text-decoration:none}

.site-header{position:absolute;top:0;left:0;width:1200px;height:112px;background:var(--white)}
.brand{position:absolute;left:112px;top:18px;display:flex;align-items:center;gap:10px}
.brand-mark{width:18px;height:18px;background:var(--blue)}
.brand-name{font-family:'Cormorant Garamond',serif;font-weight:600;font-size:29px;color:var(--blue);line-height:1.05;width:260px}
.top-bar{position:absolute;right:113px;top:22px;display:flex;align-items:center;gap:10px}
.social-dot{width:17px;height:17px;border-radius:50%;background:#6c6c6c}
.call{display:flex;align-items:center;gap:8px;margin-left:12px;font-size:17px;font-weight:500;color:#444}
.call span{color:var(--blue)}
.call svg{width:20px;height:20px}
.btn-apply-top{margin-left:20px;background:var(--blue);color:#fff;font-size:14px;font-weight:500;padding:6px 26px;border-radius:18px}
.main-nav{position:absolute;right:113px;top:74px;display:flex;gap:26px;font-size:14px;color:#555}
.main-nav .active{color:var(--blue)}

.hero{position:absolute;top:112px;left:0;width:1200px;height:555px;overflow:hidden}
.hero-photo{position:absolute;inset:0;background:linear-gradient(100deg,#2f3338 0%,#55585a 35%,#8a8780 60%,#3b3e42 100%)}
.hero-shade{position:absolute;inset:0;background:linear-gradient(90deg,rgba(0,0,0,.35),rgba(0,0,0,0) 60%)}
.hero-copy{position:absolute;left:114px;top:142px;width:500px;color:#fff}
.hero-copy h1{font-size:49px;font-weight:500;line-height:1.13}
.hero-copy p{font-size:15px;line-height:1.75;margin-top:14px}
.hero-copy .btn{display:inline-block;margin-top:18px;background:var(--blue);color:#fff;font-size:14px;font-weight:500;padding:8px 34px;border-radius:20px}
.hero-dots{position:absolute;right:58px;top:250px;display:flex;flex-direction:column;gap:14px;align-items:center}
.hero-dots i{width:9px;height:9px;border-radius:50%;background:#fff}
.hero-dots i.on{width:16px;height:16px;border:3px solid #fff;background:transparent}
.hero-wave{position:absolute;left:0;bottom:0;width:1200px;height:60px}
.scroll-cue{position:absolute;left:587px;top:647px;width:27px;height:27px;border:2px solid var(--blue);border-radius:50%;background:#fff;display:flex;align-items:center;justify-content:center}

.welcome{position:absolute;top:700px;left:0;width:1200px;text-align:center}
.welcome .brand-center{font-family:'Cormorant Garamond',serif;font-weight:600;font-size:40px;color:var(--blue);line-height:1.1;margin:0 auto;width:440px}
.welcome h2{font-size:40px;font-weight:600;color:var(--blue);margin-top:36px}
.welcome p{width:660px;margin:22px auto 0;font-size:15px;line-height:1.85;color:var(--muted)}
.pillars{display:flex;justify-content:center;gap:150px;margin-top:30px}
.pillar{width:92px;text-align:center}
.pillar .ring{width:86px;height:86px;border:3px solid var(--blue);border-radius:50%;margin:0 auto;display:flex;align-items:center;justify-content:center}
.pillar span{display:block;margin-top:24px;font-size:20px;font-weight:500;color:#555}

.services{position:absolute;top:1208px;left:0;width:1200px;height:1009px;background:var(--grey-bg)}
.section-title{font-size:40px;font-weight:500;color:var(--blue);text-align:center}
.services .section-title{margin-top:58px}
.service-grid{position:absolute;left:112px;top:146px;display:grid;grid-template-columns:repeat(3,305px);column-gap:30px;row-gap:26px}
.service-card{background:#fff;height:345px;box-shadow:0 1px 5px rgba(0,0,0,.12);padding:4px;text-align:center}
.service-photo{height:165px}
.service-card h3{font-size:20px;font-weight:500;color:var(--blue);margin-top:14px}
.service-card p{font-size:14px;line-height:1.85;color:var(--muted);margin:10px 18px 0}
.btn-outline{position:absolute;left:528px;top:917px;width:144px;height:42px;border:2px solid #555;border-radius:21px;font-size:15px;color:#444;display:flex;align-items:center;justify-content:center}

.news{position:absolute;top:2217px;left:0;width:1200px;height:588px;background:#fff}
.news-photo{position:absolute;left:112px;top:70px;width:803px;height:432px;background:linear-gradient(120deg,#3c3a36 0%,#7a6e5e 45%,#d6cdb8 100%)}
.news-card{position:absolute;left:693px;top:125px;width:392px;height:319px;background:#fff;padding:28px 26px 0 30px;border-right:5px solid var(--blue)}
.news-card h3{font-size:25px;font-weight:500;color:#2b4b70}
.news-card h4{font-size:16px;font-weight:500;color:var(--blue);line-height:1.45;margin-top:8px}
.news-card p{font-size:14px;line-height:1.75;color:var(--muted);margin-top:10px}
.news-card .btn{position:absolute;left:34px;bottom:20px;background:var(--blue);color:#fff;font-size:14px;font-weight:500;padding:8px 36px;border-radius:20px}

.team{position:absolute;top:2805px;left:0;width:1200px;height:470px;background:var(--grey-bg)}
.team .section-title{margin-top:45px}
.team-row{position:absolute;left:112px;top:136px;display:flex;gap:10px}
.member{width:236px;height:269px;position:relative}
.member-photo{position:absolute;inset:0}
.member-overlay{position:absolute;inset:0;background:rgba(42,111,182,.92);color:#fff;text-align:center;padding-top:70px}
.member-overlay strong{display:block;font-size:20px;font-weight:500}
.member-overlay small{display:block;font-size:14px;margin-top:2px}
.member-overlay hr{width:60px;border:none;border-top:1px solid #fff;margin:10px auto}
.member-overlay .links{display:flex;justify-content:center;gap:8px}
.member-overlay .links i{width:28px;height:28px;border:2px solid #fff;border-radius:50%}

.contact-band{position:absolute;top:3492px;left:0;width:1200px;height:430px;background:var(--footer)}
.contact-card{position:absolute;left:243px;top:3346px;width:716px;height:392px;background:#fff;box-shadow:0 2px 10px rgba(0,0,0,.15);text-align:center}
.contact-card h2{font-size:40px;font-weight:500;color:var(--blue);margin-top:30px}
.fields{display:flex;gap:20px;justify-content:center;margin-top:28px}
.field{width:178px;height:40px;border-radius:20px;background:var(--field);font-size:11px;color:#999;text-align:left;padding:11px 20px}
.field.message{width:574px;height:106px;border-radius:16px;margin:16px auto 0;display:block}
.btn-submit{display:inline-flex;align-items:center;justify-content:center;width:178px;height:44px;border:2px solid var(--blue);border-radius:22px;color:var(--blue);font-size:18px;font-weight:500;margin-top:36px}
.fold{position:absolute;left:0;bottom:-58px;width:58px;height:58px}

.site-footer{position:absolute;top:3770px;left:0;width:1200px;color:#fff;text-align:center}
.footer-social{display:flex;justify-content:center;gap:8px}
.footer-social i{width:31px;height:31px;border:2px solid #fff;border-radius:50%}
.footer-nav{display:flex;justify-content:center;gap:32px;font-size:14px;margin-top:14px}
.footer-rule{border:none;border-top:1px solid #3a3a3a;margin-top:18px}
.copyright{font-size:14px;margin-top:20px}
</style>
</head>
<body>

<header class="site-header">
  <a class="brand" href="#"><span class="brand-mark"></span><span class="brand-name">Corvane Lending Partners</span></a>
  <div class="top-bar">
    <i class="social-dot"></i><i class="social-dot"></i><i class="social-dot"></i><i class="social-dot"></i>
    <div class="call">
      <svg viewBox="0 0 20 20"><circle cx="10" cy="10" r="10" fill="#2a6fb6"/><path d="M7 5l2 2-1 1.5c.6 1.4 1.6 2.4 3 3L12.5 10.5l2 2-1.5 1.8C9 14 6 11 5.7 6.5z" fill="#fff"/></svg>
      Call Us: <span>(555) 318-2046</span>
    </div>
    <a class="btn-apply-top" href="#">Apply Now</a>
  </div>
  <nav class="main-nav">
    <a class="active" href="#">Home</a><a href="#">About Us</a><a href="#">Loan Programs</a><a href="#">Loan Criteria</a><a href="#">News</a><a href="#">Contact</a>
  </nav>
</header>

<section class="hero">
  <div class="hero-photo" role="img" aria-label="Photo of business advisors meeting over a laptop"></div>
  <div class="hero-shade"></div>
  <div class="hero-copy">
    <h1>Business Consulting and Training</h1>
    <p>Lorem ipsum dolor sit amet, consectetur adipiscing elit, sed do eiusmod tempor incididunt ut labore et dolore magna aliqua.</p>
    <a class="btn" href="#">Apply Now</a>
  </div>
  <div class="hero-dots"><i class="on"></i><i></i><i></i></div>
  <svg class="hero-wave" viewBox="0 0 1200 60" preserveAspectRatio="none"><path d="M0 60 L0 40 Q600 -10 1200 40 L1200 60 Z" fill="#fff"/></svg>
</section>
<div class="scroll-cue"><svg width="12" height="8" viewBox="0 0 12 8"><path d="M1 1l5 5 5-5" fill="none" stroke="#2a6fb6" stroke-width="2"/></svg></div>

<section class="welcome">
  <div class="brand-center">Corvane Lending Partners</div>
  <h2>Welcome To Corvane Lending Partners</h2>
  <p>Sed ut perspiciatis unde omnis iste natus error sit voluptatem accusantium doloremque laudantium, totam rem aperiam, eaque ipsa quae ab illo inventore veritatis et quasi architecto beatae vitae dicta sunt explicabo.</p>
  <div class="pillars">
    <div class="pillar"><div class="ring"><svg width="40" height="40" viewBox="0 0 40 40"><rect x="6" y="26" width="5" height="8" fill="#2a6fb6"/><rect x="14" y="21" width="5" height="13" fill="#2a6fb6"/><rect x="22" y="16" width="5" height="18" fill="#2a6fb6"/><rect x="30" y="10" width="5" height="24" fill="#2a6fb6"/><path d="M6 20 L20 10 L28 6" stroke="#2a6fb6" stroke-width="2" fill="none"/></svg></div><span>Growth</span></div>
    <div class="pillar"><div class="ring"><svg width="44" height="40" viewBox="0 0 44 40"><circle cx="22" cy="10" r="5" fill="#2a6fb6"/><rect x="17" y="17" width="10" height="16" rx="3" fill="#2a6fb6"/><circle cx="10" cy="14" r="4" fill="#2a6fb6"/><rect x="6" y="20" width="8" height="13" rx="3" fill="#2a6fb6"/><circle cx="34" cy="14" r="4" fill="#2a6fb6"/><rect x="30" y="20" width="8" height="13" rx="3" fill="#2a6fb6"/></svg></div><span>Leadership</span></div>
    <div class="pillar"><div class="ring"><svg width="40" height="40" viewBox="0 0 40 40"><circle cx="19" cy="21" r="14" fill="none" stroke="#2a6fb6" stroke-width="3"/><circle cx="19" cy="21" r="8" fill="none" stroke="#2a6fb6" stroke-width="3"/><circle cx="19" cy="21" r="3" fill="#2a6fb6"/><path d="M19 21 L34 6" stroke="#2a6fb6" stroke-width="2.5"/></svg></div><span>Success</span></div>
  </div>
</section>

<section class="services">
  <h2 class="section-title">Services</h2>
  <div class="service-grid">
    <article class="service-card"><div class="service-photo" role="img" aria-label="Photo of a team meeting in an office" style="background:linear-gradient(135deg,#5d6a78,#c7cdd2)"></div><h3>Working Capital</h3><p>Lorem ipsum dolor sit amet, consectetur adipiscing elit, sed do eiusmod tempor incididunt ut labore et dolore magna aliqua.</p></article>
    <article class="service-card"><div class="service-photo" role="img" aria-label="Photo of a hand stacking coins" style="background:linear-gradient(135deg,#3a3f4a,#a88b6e)"></div><h3>Debt Consolidations</h3><p>Lorem ipsum dolor sit amet, consectetur adipiscing elit, sed do eiusmod tempor incididunt ut labore et dolore magna aliqua.</p></article>
    <article class="service-card"><div class="service-photo" role="img" aria-label="Photo of a calculator and paperwork" style="background:linear-gradient(135deg,#d9d6d0,#6b6660)"></div><h3>Payroll</h3><p>Lorem ipsum dolor sit amet, consectetur adipiscing elit, sed do eiusmod tempor incididunt ut labore et dolore magna aliqua.</p></article>
    <article class="service-card"><div class="service-photo" role="img" aria-label="Photo of hands joining puzzle pieces" style="background:linear-gradient(135deg,#5f7fa8,#d4d8de)"></div><h3>Business Acquisitions</h3><p>Lorem ipsum dolor sit amet, consectetur adipiscing elit, sed do eiusmod tempor incididunt ut labore et dolore magna aliqua.</p></article>
    <article class="service-card"><div class="service-photo" role="img" aria-label="Photo of a contract being signed" style="background:linear-gradient(135deg,#8a7d6e,#e0dcd4)"></div><h3>Inventory</h3><p>Lorem ipsum dolor sit amet, consectetur adipiscing elit, sed do eiusmod tempor incididunt ut labore et dolore magna aliqua.</p></article>
    <article class="service-card"><div class="service-photo" role="img" aria-label="Photo of colleagues working at laptops" style="background:linear-gradient(135deg,#7a5a48,#d8c2ac)"></div><h3>Equipment Financing</h3><p>Lorem ipsum dolor sit amet, consectetur adipiscing elit, sed do eiusmod tempor incididunt ut labore et dolore magna aliqua.</p></article>
  </div>
  <a class="btn-outline" href="#">View More</a>
</section>

<section class="news">
  <div class="news-photo" role="img" aria-label="Photo of advisors reviewing financial charts on a tablet"></div>
  <div class="news-card">
    <h3>Recent News</h3>
    <h4>Lorem ipsum dolor sit amet, consectetur adipiscing elit, sed do eiusmod</h4>
    <p>Sed ut perspiciatis unde omnis iste natus error sit voluptatem accusantium doloremque laudantium, totam rem aperiam, eaque ipsa quae ab illo inventore veritatis et</p>
    <a class="btn" href="#">Read More</a>
  </div>
</section>

<section class="team">
  <h2 class="section-title">Our Team</h2>
  <div class="team-row">
    <div class="member"><div class="member-photo" role="img" aria-label="Headshot of a team member" style="background:linear-gradient(160deg,#6b5a4e,#b59a86)"></div></div>
    <div class="member"><div class="member-photo" role="img" aria-label="Headshot of a team member" style="background:linear-gradient(160deg,#7c8a96,#c9b8a6)"></div>
      <div class="member-overlay"><strong>Elena Marsh</strong><small>Manager</small><hr><div class="links"><i></i><i></i><i></i></div></div></div>
    <div class="member"><div class="member-photo" role="img" aria-label="Headshot of a team member" style="background:linear-gradient(160deg,#8a6a52,#d9c0a6)"></div></div>
    <div class="member"><div class="member-photo" role="img" aria-label="Headshot of a team member" style="background:linear-gradient(160deg,#4f4642,#b89c86)"></div></div>
  </div>
</section>

<div class="contact-band"></div>
<section class="contact-card">
  <h2>Contact Us</h2>
  <div class="fields"><div class="field">Name</div><div class="field">Email</div><div class="field">Phone</div></div>
  <div class="field message">Message</div>
  <a class="btn-submit" href="#">Submit</a>
  <svg class="fold" viewBox="0 0 58 58"><path d="M0 0 H58 L0 58 Z" fill="#2a6fb6"/></svg>
</section>

<footer class="site-footer">
  <div class="footer-social"><i></i><i></i><i></i></div>
  <nav class="footer-nav"><a href="#">Home</a><a href="#">About Us</a><a href="#">Loan Programs</a><a href="#">Loan Criteria</a><a href="#">News</a><a href="#">Contact</a></nav>
  <hr class="footer-rule">
  <p class="copyright">© Copyrights 2018 | All Rights Reserved</p>
</footer>

</body>
</html>
```